Custom Woodworking and Rock Design

We specialize in original, high quality, wood and rock art. It’s should be self explanatory ask questions if you need. Your team designing a logo. Furniture is custom made to order. Rocks are designed depending on consumer needs. Wood and rock can also be combined for custom work. Painted rocks on vintage wood. Custom chairs and cabinets. Artistic rocks for multiple uses:garden, magnets, custom. All ideas and requests are welcome.

Target Market(s)

All

Contact Information for Business Card

Mara Voss
Talbertstonecraft@mailbrook.net

Font styles to use
Sans Serif

Requirements
Must have
• Clear lettering
Nice to have
• Eye catching
Should not have
• Blurr

```html
<!DOCTYPE html>
<html lang="en">
<head>
<meta charset="utf-8">
<title>Talbert Stonecraft business card</title>
<link href="https://fonts.googleapis.com/css2?family=Lato:ital,wght@0,400;0,700;0,900;1,400;1,700&display=swap" rel="stylesheet">
<style>
  :root {
    --backdrop: #2b2b2b;
    --card-white: #ffffff;
    --paper: #f3f3f3;
    --band-light: #e2e2e2;
    --panel-grey: #a9a9aa;
    --bar-dark: #5b5b5d;
    --bar-mid: #6a6a6c;
    --brand-grey: #9a9a9a;
    --mark-grey: #7d7d7e;
    --text-light: #ffffff;
  }
  html, body {
    margin: 0;
    padding: 0;
    width: 1200px;
    height: 1195px;
    overflow: hidden;
    background: var(--backdrop);
    font-family: "Lato", sans-serif;
  }
  .stage {
    position: relative;
    width: 1200px;
    height: 1195px;
  }
  .card {
    position: absolute;
    left: 200px;
    width: 800px;
    height: 457px;
    border-radius: 28px;
    overflow: hidden;
    box-shadow: 0 12px 30px rgba(0,0,0,0.45);
  }
  .card--front { top: 90px; background: var(--paper); }
  .card--back { top: 630px; background: var(--card-white); }
  .card svg { display: block; }

  .front-band {
    position: absolute;
    left: 0;
    width: 100%;
    background: var(--band-light);
  }
  .front-band--top { top: 0; height: 56px; }
  .front-band--bottom { bottom: 0; height: 56px; }
  .front-name-band {
    position: absolute;
    left: 0;
    top: 300px;
    width: 100%;
    height: 72px;
    background: var(--band-light);
    display: flex;
    align-items: center;
    justify-content: center;
  }
  .brand-mark {
    position: absolute;
    background: var(--mark-grey);
  }
  .card--front .brand-mark { left: 345px; top: 120px; width: 110px; height: 110px; }
  .brand-name {
    font-weight: 700;
    color: var(--brand-grey);
    letter-spacing: 0.5px;
    text-transform: uppercase;
    white-space: nowrap;
  }
  .card--front .brand-name { font-size: 40px; }

  .back-art { position: absolute; inset: 0; }
  .bar {
    position: absolute;
    left: 0;
    background: var(--bar-dark);
    color: var(--text-light);
  }
  .bar--company {
    top: 60px; width: 330px; height: 52px;
    display: flex; align-items: center; justify-content: flex-end;
    padding-right: 18px; box-sizing: border-box;
    font-size: 27px; font-weight: 700;
  }
  .bar--person {
    top: 128px; width: 330px; height: 70px;
    padding: 8px 0 0 34px; box-sizing: border-box;
  }
  .person-name { font-size: 26px; font-weight: 700; letter-spacing: 1.5px; line-height: 1.1; }
  .person-role { font-size: 20px; font-weight: 700; }
  .bar--contact {
    top: 214px; width: 320px; height: 150px;
    background: var(--bar-mid);
    padding: 12px 0 0 20px; box-sizing: border-box;
    display: flex; flex-direction: column; gap: 10px;
  }
  .contact-line {
    display: flex; align-items: center; gap: 10px;
    font-size: 17px; font-style: italic; white-space: nowrap;
  }
  .contact-line svg { flex: none; }
  .contact-line--phone { font-size: 24px; }
  .card--back .brand-mark { left: 545px; top: 140px; width: 110px; height: 110px; }
  .card--back .brand-name {
    position: absolute; left: 360px; width: 480px; top: 270px;
    text-align: center; font-size: 32px;
  }
</style>
</head>
<body>
<main class="stage">
  <section class="card card--front" aria-label="Card front">
    <div class="front-band front-band--top"></div>
    <div class="front-band front-band--bottom"></div>
    <div class="brand-mark" aria-hidden="true"></div>
    <div class="front-name-band">
      <span class="brand-name">Talbert Stonecraft</span>
    </div>
  </section>

  <section class="card card--back" aria-label="Card back">
    <svg class="back-art" width="800" height="457" viewBox="0 0 800 457" aria-hidden="true">
      <rect width="800" height="457" fill="var(--panel-grey)"/>
      <path d="M380 0 C300 170 320 370 470 457 L800 457 L800 0 Z" fill="var(--card-white)"/>
    </svg>
    <div class="bar bar--company">Talbert Stonecraft</div>
    <div class="bar bar--person">
      <div class="person-name">MARA VOSS</div>
      <div class="person-role">Director</div>
    </div>
    <div class="bar bar--contact">
      <div class="contact-line contact-line--phone">
        <svg width="24" height="20" viewBox="0 0 24 20"><path d="M2 6 Q12 0 22 6 L20 9 L16 7 L16 5 Q12 3 8 5 L8 7 L4 9 Z" fill="#fff"/><rect x="5" y="10" width="14" height="8" rx="1" fill="#fff"/></svg>
        555-014-2270
      </div>
      <div class="contact-line">
        <svg width="24" height="16" viewBox="0 0 24 16"><rect x="1" y="1" width="22" height="14" fill="none" stroke="#fff" stroke-width="2"/><path d="M1 1 L12 9 L23 1" fill="none" stroke="#fff" stroke-width="2"/></svg>
        Talbertstonecraft@mailbrook.net
      </div>
      <div class="contact-line">
        <svg width="24" height="20" viewBox="0 0 24 20"><rect x="1" y="1" width="22" height="14" rx="1" fill="none" stroke="#fff" stroke-width="2"/><rect x="9" y="16" width="6" height="3" fill="#fff"/></svg>
        www.talbertstonecraft.net
      </div>
    </div>
    <div class="brand-mark" aria-hidden="true"></div>
    <span class="brand-name">Talbert Stonecraft</span>
  </section>
</main>
</body>
</html>
```